International Film making Business needs the 5 Logos provided made into a POSTER Format

Design Task:
CREATE A POSTER DESIGN USING THE 5 LOGOS PROVIDED. The BOLD BRIGHT HORIZON LOGO should stand out from the others by being in the middle with the other 4 logos connected to it somehow.

The 5 Businesses already has their 5 Logos, all similar in design to each other.

BOLD BRIGHT HORIZON is the Main Logo that encompasses the other 4 Logos. So it must stand out more and it is like the Overall Business entity that incorporates the other 4 Logos.

What is required is that by using the 5 Logo designs provided, create a cool graphic artwork that somehow incorporates ALL of the 5 Logos - But having the BOLD BRIGHT HORIZON Logo at the forefront/most important/standing out the most.
- BOLD BRIGHT HORIZON will probably be bigger than the others
- and could be changed into 3D.

I have attached all 5 logos and a hand drawn example of how the BOLD BRIGHT HORIZONS could stand out from the rest.

THE DESIGNS OF THE LOGOS SHOULD NOT BE CHANGED (except the BOLDBRIGHTHORIZON which can be 3D)

Please do not be restricted with the sample idea. Creativity is encouraged

DIMENSION: 3000 mm x 6000 mm
high resolution graphic

Logo Text

bold bright , bold bright pictures, bold bright legends, bold bright groovy, BOLD BRIGHT HORIZONS

Requirements
Must have
• USE THE 5 LOGOS PROVIDED ONLY - Only BOLD BRIGHT HORIZON can be changed into 3D only
Nice to have
• Eye catching design, showing the Bold Bright Horizon as the most powerful Logo that has the other 4 as subordinate companies
Should not have
• ANY CHANGE IN THE 5 LOGO DESIGNS (EXcept 3D for Bold Bright Horizons)

```html
<!DOCTYPE html>
<html lang="en">
<head>
<meta charset="utf-8">
<title>Bold Bright Horizons – Poster</title>
<link rel="stylesheet" href="https://fonts.googleapis.com/css2?family=Cinzel:wght@400;600;700&family=Questrial&display=swap">
<style>
  :root {
    --gold: #d9b24c;
    --gold-deep: #b8902f;
    --silver: #9a9a9a;
    --film-black: #141414;
    --frame-white: #ffffff;
    --page-white: #ffffff;
    --camera-dark: #1b1b1b;
    --camera-warm: #5a4318;
    --sub-blue: #1f74c9;
    --sub-dark: #222222;
    --sub-violet: #8a3fc4;
    --sub-green: #2f9a1e;
    --url-grey: #6b6b6b;
  }
  html, body {
    margin: 0;
    padding: 0;
    width: 1200px;
    height: 600px;
    overflow: hidden;
    background: var(--page-white);
  }
  .poster {
    display: block;
    width: 1200px;
    height: 600px;
  }
  .backdrop-gold { fill: var(--gold); }
  .film-band { fill: var(--film-black); }
  .film-frame { fill: var(--frame-white); }
  .camera-area { fill: url(#camera-tone); }
  .sub-name {
    font-family: "Cinzel", serif;
    font-weight: 600;
    text-anchor: middle;
  }
  .sub-name--bright { fill: var(--sub-blue); font-size: 24px; }
  .sub-name--pictures { fill: var(--sub-dark); font-size: 21px; }
  .sub-name--legends { fill: var(--sub-violet); font-size: 21px; }
  .sub-name--groovy { fill: var(--sub-green); font-size: 21px; }
  .main-mark { fill: var(--gold); }
  .main-name {
    font-family: "Cinzel", serif;
    font-weight: 600;
    fill: var(--gold-deep);
  }
  .main-url {
    font-family: "Questrial", sans-serif;
    fill: var(--url-grey);
    font-size: 25px;
  }
</style>
</head>
<body>
<svg class="poster" viewBox="0 0 1200 600" xmlns="http://www.w3.org/2000/svg">
  <defs>
    <linearGradient id="camera-tone" x1="0" y1="0" x2="0" y2="1">
      <stop offset="0" stop-color="var(--camera-dark)"/>
      <stop offset="1" stop-color="var(--camera-warm)"/>
    </linearGradient>
  </defs>

  <!-- gold backdrop -->
  <polygon class="backdrop-gold" points="0,0 760,0 760,40 0,160"/>
  <polygon class="backdrop-gold" points="0,350 455,320 500,600 0,600"/>

  <!-- film strip band with frames -->
  <g class="film-strip" transform="rotate(-8.5 0 233)">
    <rect class="film-band" x="-60" y="93" width="1360" height="280" role="img" aria-label="Film strip running across the poster"/>

    <rect class="film-frame" x="40" y="143" width="245" height="180"/>
    <text class="sub-name sub-name--bright" x="162" y="240">BOLD BRIGHT</text>

    <rect class="film-frame" x="305" y="143" width="245" height="180"/>
    <text class="sub-name sub-name--pictures" x="427" y="226">BOLD BRIGHT</text>
    <text class="sub-name sub-name--pictures" x="427" y="254">PICTURES</text>

    <rect class="film-frame" x="570" y="143" width="245" height="180"/>
    <text class="sub-name sub-name--legends" x="692" y="226">BOLD BRIGHT</text>
    <text class="sub-name sub-name--legends" x="692" y="254">LEGENDS</text>

    <rect class="film-frame" x="835" y="143" width="245" height="180"/>
    <text class="sub-name sub-name--groovy" x="957" y="226">BOLD BRIGHT</text>
    <text class="sub-name sub-name--groovy" x="957" y="254">GROOVY</text>

    <rect class="film-frame" x="1100" y="143" width="245" height="180"/>
  </g>

  <!-- film camera area -->
  <rect class="camera-area" x="62" y="278" width="325" height="290" rx="30" role="img" aria-label="Illustration of a vintage film camera with two reels projecting a beam"/>

  <!-- main company name -->
  <circle class="main-mark" cx="625" cy="445" r="95"/>
  <text class="main-name" x="763" y="453" font-size="52" textLength="380" lengthAdjust="spacingAndGlyphs">BOLD BRIGHT</text>
  <text class="main-name" x="763" y="521" font-size="60" textLength="380" lengthAdjust="spacingAndGlyphs">HORIZONS</text>
  <text class="main-url" x="764" y="553" textLength="378" lengthAdjust="spacing">boldbrighthorizons.com.au</text>
</svg>
</body>
</html>
```